Dynamic Business Card for Sports Supplements Company

Hi! I'm looking for an awesome business card to match my existing sports supplement company. I have uploaded my current company logo and screenshot of the front page of my website.

I would like to have something dynamic and interesting and utilize the colors in the website - the reds and purples

The business card should be double sided and focus on a unique eye-catching design on the back and include all the relevant company info.

Most importantly, it should say somewhere: "Sign up on our website for a coupon code."

Target Market(s)

Mostly for women gym goers but it shouldn't be too feminine. It should be in keeping with the website design. It should flow and clearly be connected to it

Industry/Entity Type

Business

Contact Information for Business Card

Lorraine K. Vestal
CEO
LVestal@Quorvanexco.com
www.quorvanexco.com
555.417.3820
P.O. Box 47315
Alden, Corvell 00000

Sign up on our website for a coupon code

Font styles to use
Serif
Sans Serif
Other font styles liked:
• Novecento font family and "Quorvanex" is in AR Destine font

Requirements
Must have
• One side should be a bold Quorvanex logo design. Even just the symbol itself may be o.k. (see attached file)

```html
<!DOCTYPE html>
<html lang="en">
<head>
<meta charset="utf-8">
<title>Quorvanex Business Card</title>
<link rel="stylesheet" href="https://fonts.googleapis.com/css2?family=Saira:wght@600;700&family=Open+Sans:wght@400;600&display=swap">
<style>
  :root {
    --brand-red: #e3232b;
    --brand-purple: #3a3478;
    --card-white: #ffffff;
    --card-black: #1f1f1f;
    --ink: #4a4a4a;
    --stage: #d9d9d9;
  }
  * { box-sizing: border-box; margin: 0; padding: 0; }
  html, body { width: 1200px; height: 1000px; overflow: hidden; }
  body {
    background: var(--stage);
    font-family: "Open Sans", Arial, sans-serif;
    display: flex;
    align-items: center;
    justify-content: center;
    gap: 40px;
  }
  .card {
    position: relative;
    width: 560px;
    height: 320px;
    overflow: hidden;
    box-shadow: 0 6px 18px rgba(0,0,0,0.25);
  }

  /* Front */
  .card-front { background: var(--card-white); }
  .brand-name {
    position: absolute;
    left: 36px;
    top: 26px;
    font-family: "Saira", Arial, sans-serif;
    font-weight: 700;
    font-size: 34px;
    line-height: 1;
    letter-spacing: 0.5px;
    text-transform: uppercase;
    color: var(--brand-red);
  }
  .tagline {
    position: absolute;
    left: 36px;
    top: 64px;
    font-size: 14px;
    letter-spacing: 0.6px;
    color: var(--brand-red);
  }
  .person {
    position: absolute;
    right: 44px;
    top: 172px;
    text-align: right;
  }
  .person-name {
    font-family: "Saira", Arial, sans-serif;
    font-weight: 700;
    font-size: 17px;
    letter-spacing: 0.4px;
    text-transform: uppercase;
    color: var(--brand-red);
    line-height: 1.1;
  }
  .rule {
    position: absolute;
    left: 36px;
    top: 199px;
    width: 480px;
    height: 2px;
    background: var(--brand-red);
  }
  .person-title {
    position: absolute;
    right: 44px;
    top: 205px;
    font-size: 11px;
    color: var(--ink);
  }
  .contact-list {
    position: absolute;
    left: 36px;
    top: 226px;
    list-style: none;
    font-size: 12px;
    color: var(--ink);
  }
  .contact-list li {
    display: flex;
    align-items: center;
    gap: 8px;
    height: 18px;
  }
  .contact-list svg { width: 11px; height: 11px; fill: var(--brand-red); flex: none; }
  .web-highlight { color: var(--brand-red); }
  .address {
    position: absolute;
    right: 44px;
    top: 242px;
    font-size: 12px;
    line-height: 17px;
    color: var(--ink);
    text-align: right;
  }
  .address svg { width: 9px; height: 9px; fill: var(--brand-red); margin-right: 10px; }
  .promo-band {
    position: absolute;
    left: 0;
    bottom: 0;
    width: 560px;
    height: 20px;
  }
  .promo-text {
    position: absolute;
    left: 40px;
    bottom: 3px;
    font-size: 10px;
    font-weight: 600;
    letter-spacing: 0.5px;
    text-transform: uppercase;
    color: var(--card-white);
  }

  /* Back */
  .card-back {
    background: var(--card-black);
    display: flex;
    flex-direction: column;
    align-items: center;
    justify-content: center;
  }
  .card-back .brand-name {
    position: static;
    color: var(--card-white);
    font-size: 40px;
  }
  .card-back .tagline {
    position: static;
    color: var(--card-white);
    font-size: 15px;
    margin-top: 6px;
  }
</style>
</head>
<body>

  <section class="card card-front" aria-label="Business card front">
    <div class="brand-name">Quorvanex</div>
    <div class="tagline">your progress companion</div>

    <div class="person"><div class="person-name">Lorraine K. Vestal</div></div>
    <div class="rule"></div>
    <div class="person-title">CEO</div>

    <ul class="contact-list">
      <li>
        <svg viewBox="0 0 24 24" aria-hidden="true"><path d="M6.6 10.8a15.1 15.1 0 0 0 6.6 6.6l2.2-2.2a1 1 0 0 1 1-.25 11.4 11.4 0 0 0 3.6.6 1 1 0 0 1 1 1V20a1 1 0 0 1-1 1A17 17 0 0 1 3 4a1 1 0 0 1 1-1h3.5a1 1 0 0 1 1 1c0 1.25.2 2.45.6 3.6a1 1 0 0 1-.25 1z"/></svg>
        555.417.3820
      </li>
      <li>
        <svg viewBox="0 0 24 24" aria-hidden="true"><path d="M2 5h20v14H2z M3.5 6.5 12 13l8.5-6.5" stroke="#fff" stroke-width="1.5"/></svg>
        LVestal@Quorvanexco.com
      </li>
      <li>
        <svg viewBox="0 0 24 24" aria-hidden="true"><path d="M14 2a8 8 0 1 1-5.3 14l-5.2 5.2-1.7-1.7 5.2-5.2A8 8 0 0 1 14 2zm0 2.5a5.5 5.5 0 1 0 0 11 5.5 5.5 0 0 0 0-11z"/></svg>
        <span>www.<span class="web-highlight">quorvanexco</span>.com</span>
      </li>
    </ul>

    <div class="address">
      <svg viewBox="0 0 10 10" aria-hidden="true"><path d="M0 4 10 0 6 10 5 5z"/></svg>P.O. Box 47315 Alden,<br>Corvell 00000
    </div>

    <svg class="promo-band" viewBox="0 0 560 20" preserveAspectRatio="none" aria-hidden="true">
      <polygon points="0,0 428,0 416,20 0,20" fill="var(--brand-red)"/>
      <polygon points="436,0 560,0 560,20 424,20" fill="var(--brand-purple)"/>
    </svg>
    <div class="promo-text">Sign up on our website for a coupon code</div>
  </section>

  <section class="card card-back" aria-label="Business card back">
    <div class="brand-name">Quorvanex</div>
    <div class="tagline">your progress companion</div>
  </section>

</body>
</html>
```